I need a business card design for a new business based in South West Australia.
I specialize in residential window cleaning & general handyman maintenance.

Dale Marsh - 412 SILVER HAWK DETAILING
- Window Cleaning
- House Maintenance

```html
<!DOCTYPE html>
<html lang="en">
<head>
<meta charset="utf-8">
<title>412 Silver Hawk Detailing – Business Card</title>
<link rel="stylesheet" href="https://fonts.googleapis.com/css2?family=Noto+Sans:wght@400;500&display=swap">
<style>
  :root {
    --page-bg: #d9d6d1;
    --card-top: #f3f4f5;
    --card-bottom: #e4e6e8;
    --ink: #141414;
    --band-grey: #4a4a4c;
    --band-tan: #b9a78d;
    --band-blue: #123a7a;
    --band-blue-deep: #0b2a5e;
    --art-light: #dcecf6;
    --art-mid: #a9d3ea;
    --mark: #1c1c1c;
  }
  * { margin: 0; padding: 0; box-sizing: border-box; }
  html, body {
    width: 1200px;
    height: 970px;
    overflow: hidden;
    background: var(--page-bg);
  }
  .business-card {
    position: absolute;
    left: 50px;
    top: 155px;
    width: 1100px;
    height: 660px;
    background: linear-gradient(180deg, var(--card-top), var(--card-bottom));
    overflow: hidden;
    font-family: "Noto Sans", sans-serif;
    color: var(--ink);
    box-shadow: 0 6px 24px rgba(0,0,0,0.18);
  }
  .cleaning-artwork {
    position: absolute;
    left: 0;
    top: 0;
    width: 450px;
    height: 500px;
    background: radial-gradient(ellipse at 55% 55%, var(--art-mid) 0%, var(--art-light) 55%, rgba(220,236,246,0) 78%);
  }
  .company-name {
    position: absolute;
    right: 48px;
    top: 78px;
    font-size: 46px;
    font-weight: 500;
    letter-spacing: 0.2px;
    white-space: nowrap;
  }
  .owner-name {
    position: absolute;
    right: 48px;
    top: 218px;
    font-size: 42px;
    font-weight: 500;
  }
  .service-list {
    position: absolute;
    right: 48px;
    top: 360px;
    list-style: none;
    text-align: right;
  }
  .service-item {
    font-size: 33px;
    line-height: 58px;
    display: flex;
    justify-content: flex-end;
    align-items: center;
    gap: 26px;
  }
  .service-marker {
    display: inline-block;
    width: 16px;
    height: 16px;
    border-radius: 50%;
    background: var(--mark);
    margin-right: 8px;
  }
  .wave-bands {
    position: absolute;
    left: 0;
    bottom: 0;
    width: 1100px;
    height: 660px;
  }
</style>
</head>
<body>
  <main class="business-card">
    <div class="cleaning-artwork" role="img" aria-label="Illustration of a window squeegee wiping a soapy bubble cloud"></div>

    <svg class="wave-bands" viewBox="0 0 1100 660" aria-hidden="true">
      <path d="M0,540 C250,528 450,578 650,576 C850,572 1000,528 1100,526 L1100,548 C900,556 700,600 450,626 C300,640 150,650 0,652 Z" fill="var(--band-grey)" opacity="0.85"/>
      <path d="M0,560 C250,548 450,596 650,594 C850,590 1000,546 1100,544" fill="none" stroke="var(--band-tan)" stroke-width="3"/>
      <defs>
        <linearGradient id="blueBand" x1="0" y1="0" x2="1" y2="1">
          <stop offset="0" stop-color="var(--band-blue)"/>
          <stop offset="1" stop-color="var(--band-blue-deep)"/>
        </linearGradient>
      </defs>
      <path d="M0,660 L0,652 C150,648 300,640 450,628 C700,604 900,560 1100,552 L1100,660 Z" fill="url(#blueBand)"/>
    </svg>

    <h1 class="company-name">412 SILVER HAWK DETAILING</h1>
    <p class="owner-name">Dale Marsh</p>
    <ul class="service-list">
      <li class="service-item">Window Cleaning <span class="service-marker" role="img" aria-label="decorative marker"></span></li>
      <li class="service-item">House Maintenance <span class="service-marker" role="img" aria-label="decorative marker"></span></li>
    </ul>
  </main>
</body>
</html>
```